Business card design for my company.
I would like the card's background colour to be black. You can also see our web site to get an idea of our brand. https://www.tmwhomecrafting.com.au/
- Name
- Email

```html
<!DOCTYPE html>
<html lang="en">
<head>
<meta charset="utf-8">
<title>TMW Home Crafting – Business Card</title>
<link rel="stylesheet" href="https://fonts.googleapis.com/css2?family=Montserrat:wght@300;400;500&display=swap">
<style>
  :root {
    --page-bg: #d8d9da;
    --card-dark: #3a3b3d;
    --brand-green: #17934a;
    --text-white: #ffffff;
    --text-soft: #e4e4e4;
    --rule-grey: #b9babb;
  }
  * { margin: 0; padding: 0; box-sizing: border-box; }
  html, body {
    width: 1200px;
    height: 1043px;
    overflow: hidden;
    background: var(--page-bg);
    font-family: "Montserrat", sans-serif;
  }
  .card {
    position: absolute;
    left: 204px;
    width: 792px;
    height: 437px;
    background: var(--card-dark);
    overflow: hidden;
  }
  .card--front { top: 98px; }
  .card--back { top: 582px; }

  .front-panel { position: absolute; inset: 0; }

  .edge-tab {
    position: absolute;
    left: 0;
    width: 7px;
    background: var(--brand-green);
    border-radius: 0 4px 4px 0;
  }
  .edge-tab--top { top: 45px; height: 59px; }
  .edge-tab--bottom { top: 349px; height: 61px; }

  .holder {
    position: absolute;
    left: 41px;
    top: 42px;
  }
  .holder__name {
    font-size: 35px;
    font-weight: 400;
    color: var(--text-white);
    line-height: 1;
  }
  .holder__title {
    margin-top: 10px;
    font-size: 17px;
    font-weight: 400;
    color: var(--text-soft);
    line-height: 1;
    padding-bottom: 8px;
    border-bottom: 2px solid var(--brand-green);
    width: 140px;
  }

  .contact-list {
    position: absolute;
    left: 46px;
    top: 339px;
    list-style: none;
  }
  .contact-list li {
    display: flex;
    align-items: center;
    height: 23px;
    font-size: 17px;
    color: var(--text-soft);
  }
  .contact-list svg {
    width: 13px;
    height: 13px;
    margin-right: 14px;
    fill: var(--brand-green);
  }

  .front-wordmark {
    position: absolute;
    right: 36px;
    top: 372px;
    font-size: 20px;
    font-weight: 500;
    color: var(--text-white);
    letter-spacing: 1px;
  }

  .back-wordmark {
    position: absolute;
    left: 0;
    right: 0;
    top: 178px;
    text-align: center;
    font-size: 44px;
    font-weight: 500;
    letter-spacing: 4px;
    color: var(--text-white);
  }

  .web-line {
    position: absolute;
    left: 37px;
    right: 45px;
    top: 380px;
    display: flex;
    align-items: center;
    gap: 16px;
  }
  .web-line__rule {
    flex: 1;
    height: 1px;
    background: var(--rule-grey);
  }
  .web-line__url {
    font-size: 17px;
    font-weight: 400;
    color: var(--text-soft);
    white-space: nowrap;
  }
  .web-line__url em {
    font-style: normal;
    color: var(--brand-green);
  }
</style>
</head>
<body>

<section class="card card--front" aria-label="Business card front">
  <svg class="front-panel" viewBox="0 0 792 437" width="792" height="437" aria-hidden="true">
    <polygon points="443,0 792,0 792,437 531,437 339,153" fill="var(--brand-green)"/>
  </svg>

  <span class="edge-tab edge-tab--top"></span>
  <span class="edge-tab edge-tab--bottom"></span>

  <div class="holder">
    <p class="holder__name">Liam Harcourt</p>
    <p class="holder__title">General Manager</p>
  </div>

  <ul class="contact-list">
    <li>
      <svg viewBox="0 0 24 24" aria-hidden="true"><path d="M6.6 10.8a15.1 15.1 0 0 0 6.6 6.6l2.2-2.2a1 1 0 0 1 1-.25 11.4 11.4 0 0 0 3.6.57 1 1 0 0 1 1 1V20a1 1 0 0 1-1 1A17 17 0 0 1 3 4a1 1 0 0 1 1-1h3.5a1 1 0 0 1 1 1c0 1.25.2 2.45.57 3.57a1 1 0 0 1-.25 1z"/></svg>
      0400 555 318
    </li>
    <li>
      <svg viewBox="0 0 24 24" aria-hidden="true"><path d="M2 5h20v14H2z M2 5l10 8 10-8" /></svg>
      info@tmwhomecrafting.com.au
    </li>
    <li>
      <svg viewBox="0 0 24 24" aria-hidden="true"><path d="M12 2a7 7 0 0 0-7 7c0 5.2 7 13 7 13s7-7.8 7-13a7 7 0 0 0-7-7zm0 9.5A2.5 2.5 0 1 1 12 6.5a2.5 2.5 0 0 1 0 5z"/></svg>
      Kingston, Tasmania, Australia
    </li>
  </ul>

  <p class="front-wordmark">TMW Home Crafting</p>
</section>

<section class="card card--back" aria-label="Business card back">
  <p class="back-wordmark">TMW HOME CRAFTING</p>

  <div class="web-line">
    <span class="web-line__rule"></span>
    <span class="web-line__url">www.<em>tmwhomecrafting</em>.com</span>
    <span class="web-line__rule"></span>
  </div>
</section>

</body>
</html>
```